Halvern Studio Works New Business Card

I am opening a new division of my business. I am a high end interior designer, and the new business is writing specs for construction projects. It will be marketed to the VERY high end contractor, architects and realtors. The client will actually be the one who pays us and signs the agreement, but it will be the contractor, architect or realtor that will recommend us. I have attached my current card and our previous logo which is still used on some of our paperwork. I would like the new logo to be connected in some way to what we are currently using. We will need to have room on the card for a person's name. I'd like to omit the address as we might be moving the office soon. The web address is www.HalvernStudioWorks.com. For this design, please use my name, Marisol Thornbury.

Target Market(s)

High End Luxury Contractors, Realtors and Architects

Industry/Entity Type

Residential Construction

Contact Information for Business Card

Halvern Studio Works, Phone: 555-214-9087, www.HalvernStudioWorks.com , Marisol Thornbury

Font styles to use
Sans Serif

Colors
ec1f27

Requirements
Must have
• Some visual reference to my current card and logos. Use the colors submitted on the business card I attached.
Nice to have
• A visual reference to my current card and logos. Use the colors submitted on the card I attached.
Should not have
• A physical address

```html
<!DOCTYPE html>
<html lang="en">
<head>
<meta charset="utf-8">
<title>Halvern Studio Works – Business Card</title>
<link rel="stylesheet" href="https://fonts.googleapis.com/css2?family=Source+Sans+3:wght@300;400;600&display=swap">
<style>
  :root {
    --backdrop: #2f2620;
    --card: #fbfbfa;
    --rust: #a9401c;
    --accent-red: #c2401e;
    --logo-grey: #a3a3a3;
    --text-grey: #5a5a5a;
    --fold: #e4e4e2;
  }
  * { margin: 0; padding: 0; box-sizing: border-box; }
  html, body {
    width: 1200px; height: 794px; overflow: hidden;
    background: var(--backdrop);
    font-family: "Source Sans 3", sans-serif;
  }
  .canvas {
    width: 1200px; height: 794px;
    display: flex; align-items: center; justify-content: center; gap: 48px;
  }
  .card {
    width: 520px; height: 297px;
    background: var(--card);
    box-shadow: 0 10px 30px rgba(0,0,0,.45);
    position: relative;
    display: flex;
  }
  .brand {
    display: flex; align-items: center; gap: 14px;
  }
  .brand-square {
    background: var(--rust);
    flex: none;
  }
  .brand-name {
    color: var(--logo-grey);
    font-weight: 300;
    text-transform: uppercase;
    line-height: 1.02;
    letter-spacing: .02em;
  }
  /* front */
  .card--front { align-items: center; justify-content: center; }
  .card--front .brand-square { width: 78px; height: 62px; }
  .card--front .brand-name { font-size: 36px; }
  /* back */
  .card--back .half {
    flex: 1; display: flex; align-items: center; justify-content: center;
  }
  .card--back .half + .half { border-left: 1px solid var(--fold); justify-content: flex-start; padding-left: 30px; }
  .card--back .brand { gap: 9px; }
  .card--back .brand-square { width: 44px; height: 35px; }
  .card--back .brand-name { font-size: 20px; }
  .contact { color: var(--text-grey); font-size: 13.5px; line-height: 1.3; }
  .contact-name { color: var(--accent-red); font-weight: 600; font-size: 19px; margin-bottom: 2px; }
  .contact-role { margin-bottom: 8px; }
  .contact-label { color: var(--accent-red); font-weight: 600; }
  .contact-web { font-weight: 600; margin-top: 2px; }
</style>
</head>
<body>
<main class="canvas">
  <section class="card card--front" aria-label="Card front">
    <div class="brand">
      <span class="brand-square"></span>
      <span class="brand-name">Halvern Studio<br>Works</span>
    </div>
  </section>

  <section class="card card--back" aria-label="Card back">
    <div class="half">
      <div class="brand">
        <span class="brand-square"></span>
        <span class="brand-name">Halvern Studio<br>Works</span>
      </div>
    </div>
    <div class="half">
      <div class="contact">
        <p class="contact-name">Marisol Thornbury</p>
        <p class="contact-role">Professional Specifications<br>for Contractors</p>
        <p><span class="contact-label">Office:</span> 555.214.9087</p>
        <p><span class="contact-label">Cell:</span> 555.214.3361</p>
        <p class="contact-web">www.HalvernStudioWorks.com</p>
      </div>
    </div>
  </section>
</main>
</body>
</html>
```